Business card design Needed for new logo / Construction business, home extensions and new builds

We need a business card design using our new logo files which i will attach to this project :)

We are a small construction business specialising in home extensions, new builds and property development. We are very ambitious and would appreciate professional and elegant designs for our new business card.

Very serious about using the services on MakerQuarry and recently acquired our new logo from here :)

Please get involved, i will feedback when i can as i am very busy but can respond daily, thanks

Target Market(s)

People that want to build onto their houses, new building developments or adding too their existing property

Industry/Entity Type

Construction

Contact Information for Business Card

Renwick Tolliver Construction, Lionel Ashby (Managing Director), Tel 07822254961, email - info@renwick-tolliver, www.renwick-tolliver.co.uk

Colors

Designer to choose colors to be used in the design.

Requirements
Must have
• I like a deep grey on the back please. A lot of you have provided black from and back, try mixing things up a little. The black looks cool 😎 Thanks

```html
<!DOCTYPE html>
<html lang="en">
<head>
<meta charset="utf-8">
<title>Renwick Tolliver Construction – Business Card</title>
<link rel="stylesheet" href="https://fonts.googleapis.com/css2?family=Cinzel:wght@400;600&family=Montserrat:wght@400;600;700&display=swap">
<style>
  :root{
    --stage:#3b3b3d;
    --gold-light:#e9bd66;
    --gold:#d9a74a;
    --gold-deep:#b9852c;
    --card-grey:#232325;
    --mark-grey:#2c2c2f;
    --ink-white:#ffffff;
    --soft-white:#e8e8e8;
  }
  *{margin:0;padding:0;box-sizing:border-box}
  html,body{width:1200px;height:689px;overflow:hidden}
  body{background:var(--stage);position:relative;font-family:"Montserrat",sans-serif}
  .card{position:absolute;top:190px;width:540px;height:309px;border-radius:22px;overflow:hidden}
  .card--front{left:34px}
  .card--back{left:626px;background:var(--card-grey)}

  .front-pattern{position:absolute;inset:0;background:linear-gradient(135deg,var(--gold-light),var(--gold) 55%,var(--gold-deep))}
  .front-brand{position:absolute;inset:0;display:flex;flex-direction:column;align-items:center;justify-content:center;color:var(--ink-white)}
  .brand-square{display:block;background:currentColor}
  .front-brand .brand-square{width:62px;height:62px;margin-bottom:18px}
  .front-brand__name{font-family:"Cinzel",serif;font-weight:600;font-size:34px;letter-spacing:1px;line-height:1}
  .tagline{display:flex;align-items:center;gap:10px;margin-top:10px;font-family:"Cinzel",serif;font-weight:400;letter-spacing:3px}
  .tagline::before,.tagline::after{content:"";width:34px;height:1.5px;background:currentColor}
  .front-brand .tagline{font-size:19px}

  .back-accent{position:absolute;right:30px;top:28px;width:10px;height:40px;background:linear-gradient(180deg,var(--gold-light),var(--gold-deep))}
  .person{position:absolute;right:50px;top:28px;text-align:right}
  .person__name{font-weight:700;font-size:21px;color:var(--gold);letter-spacing:.5px;line-height:1.1}
  .person__role{font-size:12px;color:var(--soft-white);letter-spacing:.4px;margin-top:2px}

  .back-mark{position:absolute;right:52px;top:118px;width:120px;height:120px;background:var(--mark-grey);border-radius:4px}

  .back-brand{position:absolute;left:34px;top:84px;color:var(--gold)}
  .back-brand .brand-square{width:38px;height:38px;margin-bottom:12px}
  .back-brand__name{font-family:"Cinzel",serif;font-weight:600;font-size:22px;letter-spacing:.5px;line-height:1}
  .back-brand .tagline{font-size:12px;margin-top:6px;gap:8px}
  .back-brand .tagline::before,.back-brand .tagline::after{width:22px}

  .contact{position:absolute;left:34px;top:196px;color:var(--soft-white);font-size:12.5px;line-height:1.45;letter-spacing:.3px}
  .contact__address{margin-bottom:8px}
  .contact__row{display:flex;align-items:center;gap:8px}
  .contact__row svg{width:12px;height:12px;flex:none}
</style>
</head>
<body>
  <section class="card card--front">
    <div class="front-pattern" role="img" aria-label="Embossed gold repeating monogram pattern"></div>
    <div class="front-brand">
      <span class="brand-square"></span>
      <div class="front-brand__name">Renwick Tolliver</div>
      <div class="tagline">CONSTRUCTION</div>
    </div>
  </section>

  <section class="card card--back">
    <div class="back-accent"></div>
    <div class="person">
      <div class="person__name">LIONEL ASHBY</div>
      <div class="person__role">Managing Director</div>
    </div>

    <div class="back-mark"></div>

    <div class="back-brand">
      <span class="brand-square"></span>
      <div class="back-brand__name">Renwick Tolliver</div>
      <div class="tagline">CONSTRUCTION</div>
    </div>

    <div class="contact">
      <div class="contact__address">Your address, City<br>State, Zip 1234</div>
      <div class="contact__row">
        <svg viewBox="0 0 24 24" fill="var(--gold)"><path d="M6.6 10.8a15.1 15.1 0 0 0 6.6 6.6l2.2-2.2c.3-.3.7-.4 1-.2 1.1.4 2.3.6 3.6.6.6 0 1 .4 1 1V20c0 .6-.4 1-1 1A17 17 0 0 1 3 4c0-.6.4-1 1-1h3.5c.6 0 1 .4 1 1 0 1.3.2 2.5.6 3.6.1.3 0 .7-.2 1z"/></svg>
        <span>07822254961</span>
      </div>
      <div class="contact__row">
        <svg viewBox="0 0 24 24" fill="var(--gold)"><path d="M2 5h20v14H2z"/><path d="M2 5l10 8 10-8" fill="none" stroke="var(--card-grey)" stroke-width="2"/></svg>
        <span>info@renwick-tolliver</span>
      </div>
      <div class="contact__row">
        <svg viewBox="0 0 24 24" fill="none" stroke="var(--gold)" stroke-width="2"><circle cx="12" cy="12" r="9"/><path d="M3 12h18M12 3c3 3 3 15 0 18M12 3c-3 3-3 15 0 18"/></svg>
        <span>www.renwick-tolliver.co.uk</span>
      </div>
    </div>
  </section>
</body>
</html>
```